Brimlow Plumbing Solutions

This is for my new plumbing company, I have attached an example of what I’m going for but want it to look better.

Target Market(s)

Home owners, real estate, etc.

Industry/Entity Type

Plumbing

Font styles to use
Other font styles liked:
• As per my logo and other examples uploaded

Colors

Designer to choose colors to be used in the design.

Requirements
Must have
• Must include my logo provided and similar to my flyer I have attached but better

```html
<!DOCTYPE html>
<html lang="en">
<head>
<meta charset="utf-8">
<title>Brimlow Plumbing Solutions – Flyer</title>
<link rel="stylesheet" href="https://fonts.googleapis.com/css2?family=Montserrat:wght@500;700&family=Inter:wght@400;500&display=swap">
<style>
  :root{
    --navy:#0b2a5c;
    --navy-deep:#082149;
    --blue:#1f7ad6;
    --sky:#38b4ee;
    --sky-soft:#5fc4f2;
    --ink:#10264d;
    --text:#1d2a3a;
    --white:#ffffff;
    --page:#eef2f7;
  }
  *{box-sizing:border-box;margin:0;padding:0}
  html,body{width:1200px;height:1200px;overflow:hidden;background:var(--page)}
  .flyer{
    position:absolute;left:282px;top:93px;width:636px;height:1014px;
    background:var(--white);overflow:hidden;
    box-shadow:0 18px 40px rgba(8,33,73,.18);
    font-family:"Inter",sans-serif;color:var(--text);
  }
  .flyer-shapes{position:absolute;inset:0}
  .brand{position:absolute;left:47px;top:38px;color:var(--white);font-family:"Montserrat",sans-serif;font-weight:700;line-height:1.05}
  .brand-line-1{display:block;font-size:30px;letter-spacing:.5px}
  .brand-line-2{display:block;font-size:21px}
  .brand-line-3{display:block;font-size:12px;margin-top:4px;letter-spacing:.3px}
  .tagline{position:absolute;left:47px;top:160px;width:235px;color:var(--white);font-size:21px;line-height:1.3;font-weight:400}
  .services-title{position:absolute;left:53px;top:472px;font-family:"Montserrat",sans-serif;font-weight:700;font-size:35px;color:var(--ink)}
  .services-rule{position:absolute;left:53px;top:521px;width:348px;height:2px;background:var(--sky)}
  .service{position:absolute;display:flex;align-items:center;gap:10px;font-size:17px;color:var(--text);line-height:1.2}
  .service svg{flex:none;width:40px;height:40px}
  .service-icon path,.service-icon circle,.service-icon rect{fill:none;stroke:var(--sky);stroke-width:1.6;stroke-linecap:round;stroke-linejoin:round}
  .contact-title{position:absolute;left:56px;top:882px;font-family:"Montserrat",sans-serif;font-weight:500;font-size:26px;color:var(--white)}
  .contact-item{position:absolute;display:flex;align-items:center;gap:6px;font-size:13px;color:var(--white);white-space:nowrap}
  .contact-item svg{width:14px;height:14px}
  .contact-item path,.contact-item circle,.contact-item rect{fill:none;stroke:var(--white);stroke-width:1.6}
  .cta-button{position:absolute;left:454px;top:920px;width:148px;height:31px;border-radius:16px;background:var(--navy);color:var(--white);font-family:"Montserrat",sans-serif;font-weight:700;font-size:12px;display:flex;align-items:center;justify-content:center}
</style>
</head>
<body>
<main class="flyer">
  <svg class="flyer-shapes" viewBox="0 0 636 1014" width="636" height="1014">
    <defs>
      <linearGradient id="photoTone" x1="0" y1="0" x2="1" y2="1">
        <stop offset="0" stop-color="#d9dde2"/>
        <stop offset=".55" stop-color="#9aa3ad"/>
        <stop offset="1" stop-color="#2f8fe0"/>
      </linearGradient>
      <linearGradient id="footerTone" x1="0" y1="0" x2="1" y2="1">
        <stop offset="0" stop-color="#1f72cf"/>
        <stop offset="1" stop-color="#3cc0f2"/>
      </linearGradient>
    </defs>
    <rect class="header-bg" x="0" y="0" width="636" height="520" fill="var(--navy)"/>
    <polygon class="header-facet" points="180,0 330,0 230,470 80,470" fill="#0f3470"/>
    <polygon class="header-stripe" points="300,115 380,115 230,440 160,440" fill="var(--blue)"/>
    <polygon class="service-photo" role="img" aria-label="Photo of running taps filling a bright blue bathtub" points="330,0 636,0 636,470 230,470" fill="url(#photoTone)"/>
    <polygon points="318,120 338,120 200,470 180,470" fill="var(--sky)"/>
    <path class="wave-accent" d="M0 400 C120 330 240 360 330 420 C420 480 540 440 636 380 L636 520 L0 520 Z" fill="var(--sky)"/>
    <path class="wave-white" d="M0 430 C120 360 230 380 330 445 C430 505 545 470 636 410 L636 1014 L0 1014 Z" fill="var(--white)"/>
    <path class="footer-accent" d="M0 860 C140 800 300 790 420 815 C520 835 590 820 636 790 L636 1014 L0 1014 Z" fill="var(--sky-soft)" opacity=".7"/>
    <path class="footer-bg" d="M0 875 C140 820 300 810 420 832 C520 850 590 835 636 808 L636 1014 L0 1014 Z" fill="url(#footerTone)"/>
  </svg>

  <div class="brand">
    <span class="brand-line-1">BRIMLOW</span>
    <span class="brand-line-2">PLUMBING</span>
    <span class="brand-line-3">SOLUTIONS</span>
  </div>
  <p class="tagline">Your local expert for Plumbing, Drainage, and Gas Maintenance.</p>

  <h2 class="services-title">Our Services</h2>
  <div class="services-rule"></div>

  <div class="service" style="left:66px;top:566px">
    <svg class="service-icon" viewBox="0 0 40 40"><path d="M20 3 35 11.5 35 28.5 20 37 5 28.5 5 11.5Z"/><path d="M14 24 20 14 26 24Z"/></svg>Emergency Plumbing</div>
  <div class="service" style="left:66px;top:626px">
    <svg class="service-icon" viewBox="0 0 40 40"><path d="M20 3 35 11.5 35 28.5 20 37 5 28.5 5 11.5Z"/><path d="M14 14 26 26M26 14 14 26"/></svg>Drain Cleaning</div>
  <div class="service" style="left:66px;top:686px">
    <svg class="service-icon" viewBox="0 0 40 40"><path d="M20 3 35 11.5 35 28.5 20 37 5 28.5 5 11.5Z"/><circle cx="16" cy="21" r="4"/><circle cx="24" cy="19" r="3"/></svg>Hot Water Systems</div>
  <div class="service" style="left:66px;top:746px">
    <svg class="service-icon" viewBox="0 0 40 40"><path d="M20 3 35 11.5 35 28.5 20 37 5 28.5 5 11.5Z"/><path d="M20 13 C16 19 15 21 15 23 A5 5 0 0 0 25 23 C25 21 24 19 20 13Z"/></svg>Leaking Fixtures</div>

  <div class="service" style="left:368px;top:566px">
    <svg class="service-icon" viewBox="0 0 40 40"><path d="M20 3 35 11.5 35 28.5 20 37 5 28.5 5 11.5Z"/><path d="M15 26 24 15M24 15 27 18"/></svg>Drainage Maintenance</div>
  <div class="service" style="left:368px;top:626px">
    <svg class="service-icon" viewBox="0 0 40 40"><path d="M20 3 35 11.5 35 28.5 20 37 5 28.5 5 11.5Z"/><rect x="14" y="13" width="12" height="14" rx="2"/><circle cx="20" cy="19" r="2.5"/></svg>Gas Maintenance</div>
  <div class="service" style="left:368px;top:680px">
    <svg class="service-icon" viewBox="0 0 40 40"><path d="M20 3 35 11.5 35 28.5 20 37 5 28.5 5 11.5Z"/><rect x="15" y="14" width="10" height="12" rx="3"/></svg>Blocked Sewer &amp;<br>Stormwater</div>
  <div class="service" style="left:368px;top:746px">
    <svg class="service-icon" viewBox="0 0 40 40"><path d="M20 3 35 11.5 35 28.5 20 37 5 28.5 5 11.5Z"/><rect x="12" y="16" width="12" height="9" rx="1.5"/><path d="M24 19 29 17 29 24 24 22"/></svg>Camera &amp; Location</div>

  <h3 class="contact-title">Contact &amp; Call to Action</h3>
  <div class="contact-item" style="left:56px;top:925px">
    <svg viewBox="0 0 14 14"><path d="M3 1.5 5 1.5 6 4.5 4.5 5.5C5.3 7.3 6.7 8.7 8.5 9.5L9.5 8 12.5 9 12.5 11C12.5 12 11.5 12.5 10.5 12.5 5.5 12 2 8.5 1.5 3.5 1.5 2.5 2 1.5 3 1.5Z"/></svg>0400 555 019</div>
  <div class="contact-item" style="left:233px;top:925px">
    <svg viewBox="0 0 14 14"><rect x="1.5" y="3" width="11" height="8" rx="1.5"/><path d="M1.5 4 7 8 12.5 4"/></svg>info@brimlow.example</div>
  <div class="contact-item" style="left:56px;top:947px">
    <svg viewBox="0 0 14 14"><circle cx="7" cy="7" r="5.5"/><path d="M1.5 7H12.5M7 1.5C4.5 4.5 4.5 9.5 7 12.5M7 1.5C9.5 4.5 9.5 9.5 7 12.5"/></svg>brimlow.example</div>
  <div class="contact-item" style="left:233px;top:947px">
    <svg viewBox="0 0 14 14"><circle cx="7" cy="7" r="5.5"/></svg>BrimlowPlumbingCo</div>

  <div class="cta-button">CALL TO ACTION</div>
</main>
</body>
</html>
```